need corporate, modern business card created for Consulting Company

I need a slick business card using elements from my website, as well as, integrating my pixelforge-created logo (see files).

The business card needs to be:
1. Corporate and modern
2. Clean and professional

I've included a PSD with the logo/icon that you can use to create it. Feel free to try a metallic finish on the logo, make it bigger/small, underlay it. Whatever you need to do to make my card stand out.

Try a black background, or white background or gray.

The idea is for my card to be memorable as well as professional and corporate.

Target Market(s)

Corporate business in the US and Canada.

Industry/Entity Type

Business

Contact Information for Business Card

Commerce Advancing Methods
Martin Coles, Senior Partner
office: 1 877 555 0143
mobile: 1 519 555 0172
website: http://www.brightvale.example

Requirements
Must have
• Card-related information
• corporate, yet modern
• clean and professional
• incorporate the icon only
• must have an editable form when complete!
Nice to have
• metallic icon might be cool
• try it with white or black

```html
<!DOCTYPE html>
<html lang="en">
<head>
<meta charset="utf-8">
<title>Commerce Advancing Methods – Business Card Back</title>
<link href="https://fonts.googleapis.com/css2?family=PT+Sans:wght@400;700&display=swap" rel="stylesheet">
<style>
  :root {
    --card-black: #15171b;
    --card-black-deep: #0b0c0e;
    --chrome: #c3c8cd;
    --chrome-edge: #0d1a22;
    --glow-blue: #2b8fc4;
    --curl-blue: #0d56a6;
    --curl-blue-light: #2a78c8;
  }
  html, body {
    margin: 0;
    padding: 0;
    width: 1200px;
    height: 685px;
    overflow: hidden;
    background: #000;
  }
  .card {
    position: relative;
    width: 1200px;
    height: 685px;
    overflow: hidden;
    background: radial-gradient(ellipse at 50% 40%, #1d2025 0%, var(--card-black) 55%, var(--card-black-deep) 100%);
    font-family: "PT Sans", "Trebuchet MS", sans-serif;
  }
  .chrome-text {
    color: var(--chrome);
    -webkit-text-stroke: 1px var(--chrome-edge);
    text-shadow:
      0 0 2px var(--glow-blue),
      1px 1px 0 var(--glow-blue),
      -1px -1px 0 var(--glow-blue),
      0 3px 4px rgba(0,0,0,0.8);
  }
  .brand {
    position: absolute;
    left: 0;
    right: 0;
    top: 150px;
    text-align: center;
  }
  .brand-square {
    display: block;
    width: 58px;
    height: 58px;
    margin: 0 auto 22px;
    border-radius: 8px;
    background: var(--chrome);
  }
  .brand-name {
    font-weight: 700;
    font-size: 40px;
    letter-spacing: 1px;
    color: var(--chrome);
  }
  .website {
    position: absolute;
    left: 0;
    right: 0;
    top: 382px;
    text-align: center;
    font-weight: 700;
    font-size: 60px;
    letter-spacing: 2px;
  }
  .contacts {
    position: absolute;
    left: 228px;
    top: 535px;
    display: flex;
    align-items: center;
    gap: 52px;
    font-weight: 700;
    font-size: 36px;
  }
  .contact {
    display: flex;
    align-items: center;
    gap: 16px;
  }
  .contact-icon {
    width: 26px;
    height: 30px;
  }
  .page-curl {
    position: absolute;
    left: 0;
    top: 0;
  }
</style>
</head>
<body>
  <div class="card">
    <div class="brand">
      <span class="brand-square"></span>
      <span class="brand-name">Commerce Advancing Methods</span>
    </div>

    <div class="website chrome-text">www.brightvale.example</div>

    <div class="contacts">
      <div class="contact">
        <svg class="contact-icon" viewBox="0 0 26 30" aria-label="Mobile">
          <rect x="4" y="3" width="17" height="24" rx="2" fill="none" stroke="#c3c8cd" stroke-width="3"/>
        </svg>
        <span class="chrome-text">1 519 555 0172</span>
      </div>
      <div class="contact">
        <svg class="contact-icon" viewBox="0 0 26 30" aria-label="Office">
          <path d="M19 7 C12 5 7 9 7 15 C7 21 12 25 19 23 L18 19 C14 20 12 18 12 15 C12 12 14 10 18 11 Z" fill="#c3c8cd"/>
        </svg>
        <span class="chrome-text">1 877 555 0143</span>
      </div>
    </div>

    <svg class="page-curl" width="1200" height="685" viewBox="0 0 1200 685">
      <defs>
        <linearGradient id="curlFill" x1="0" y1="0" x2="1" y2="1">
          <stop offset="0" stop-color="var(--curl-blue-light)"/>
          <stop offset="1" stop-color="var(--curl-blue)"/>
        </linearGradient>
      </defs>
      <path d="M1200 378 C1150 440 1060 500 968 521 C1000 590 1020 640 1037 685 L1200 685 Z" fill="#000" opacity="0.6"/>
      <path d="M1200 372 C1150 436 1062 492 968 521 C1010 560 1070 600 1200 612 Z" fill="url(#curlFill)"/>
    </svg>
  </div>
</body>
</html>
```